Cutting Edge Property Services Provider is Looking to Update Business Card Design

We are looking to freshen up our business cards to match our cutting edge technology based image.

KORVANEX - Where Care Finds Its Pulse

More information about our company can be found on our website at www.korvanex-demo.net

We integrate technology in a historically low tech industry.

We have appeared on the Brisk 300/3000 list 2 years in a row and we're previously recognized as the 5th Quickest Rising Firm in San Diego.

Our core colors are blue and white, but are not against accents that might improve our image.

We currently have our Mission Statement on our Business Cards in a folding design:
KORVANEX IS THE LEADING BUILDING SERVICES INNOVATOR. BY COMBINING TECHNOLOGY WITH FUNCTIONAL TOOS THAT IMPROVE EFFICIENCY IN THE WORKPLACE, WE PROVIDE UNPARALLELED SERVICE IN THE INDUSTRY. DEVELOPING LASTING RELATIONSHIPS WITH OUR CLIENTS AND ASSOCIATES IS THE CORNERSTONE OF OUR SUCCESS.

We'd like to convey the image of a cutting edge, technology based company. Want the cards to pop.

Target Market(s)

Commercial Property Managers - 20 to 50 year old professionals

Industry/Entity Type

Business

Requirements
Must have
• Must utilize our logo obviously, but are definitely open to using variations on the logo. Utilizing the components of the logo, but maybe in different configurations or backgrounds, etc...

Must use the Name: KORVANEX.
Can also use KORVANEX PROPERTY SERVICES.

Must include the Mission Statement

Must say: Where Care Finds Its Pulse
Nice to have
• We are considering plastic stock, shaped cards, or folding cards.

Nothing over the top or really expensive, but will consider if it conveys innovation and technology.
Should not have
• No images of toilets, buildings, trees, or anything relating to commercial properties.

We want to convey our technology image.

```html
<!DOCTYPE html>
<html lang="en">
<head>
<meta charset="utf-8">
<title>KORVANEX Business Card</title>
<link href="https://fonts.googleapis.com/css2?family=Jost:wght@400;500;700&display=swap" rel="stylesheet">
<style>
  :root {
    --backdrop: #8d5d39;
    --label: #1c120b;
    --card-white: #ffffff;
    --card-black: #000000;
    --brand-blue: #0b4b7c;
    --ink: #3a3a3a;
    --paper-text: #ffffff;
    --rule: #6b6b6b;
  }
  * { margin: 0; padding: 0; box-sizing: border-box; }
  html, body { width: 1200px; height: 713px; overflow: hidden; }
  body {
    position: relative;
    background: var(--backdrop);
    font-family: "Jost", "Futura", sans-serif;
  }
  .side-label {
    position: absolute; top: 28px; width: 200px;
    text-align: center; font-size: 22px; color: var(--label);
  }
  .side-label--front { left: 222px; }
  .side-label--back { left: 803px; }

  .card {
    position: absolute; width: 526px; height: 298px;
    border-radius: 22px; overflow: hidden;
  }
  .card--light { background: var(--card-white); }
  .card--dark { background: var(--card-black); }
  .card--front-cover { left: 54px; top: 72px; }
  .card--front-inside { left: 54px; top: 372px; }
  .card--back-cover { left: 640px; top: 72px; }
  .card--back-details { left: 640px; top: 372px; }

  .brand {
    position: absolute; display: flex; align-items: center; gap: 16px;
    font-weight: 700; color: var(--brand-blue); letter-spacing: 3px;
  }
  .brand__square { background: var(--brand-blue); flex: none; }
  .card--front-cover .brand { left: 0; right: 0; top: 108px; justify-content: center; font-size: 46px; }
  .card--front-cover .brand__square { width: 56px; height: 56px; }
  .card--back-cover .brand { left: 0; right: 0; top: 118px; justify-content: center; font-size: 30px; }
  .card--back-cover .brand__square { width: 36px; height: 36px; }
  .card--back-details .brand { left: 37px; top: 68px; font-size: 30px; }
  .card--back-details .brand__square { width: 36px; height: 36px; }

  .tagline {
    position: absolute; left: 0; right: 0; top: 245px;
    text-align: center; color: var(--paper-text); font-size: 18px;
  }
  .mission {
    position: absolute; left: 40px; right: 40px; top: 83px;
    text-align: center; color: var(--ink); font-size: 16.5px; line-height: 22.6px;
  }

  .holder {
    position: absolute; left: 35px; top: 212px; right: 24px;
    color: var(--paper-text); font-size: 17px;
    border-bottom: 1px solid var(--rule); padding-bottom: 2px;
  }
  .holder__role { font-size: 13px; }
  .contact { position: absolute; color: var(--paper-text); font-size: 13.5px; line-height: 20px; }
  .contact--phones { left: 35px; top: 240px; }
  .contact--web { left: 203px; top: 240px; }
  .contact--address { right: 24px; top: 244px; text-align: right; }
  .contact__row { display: flex; align-items: center; gap: 7px; }
  .contact__icon { width: 10px; height: 10px; flex: none; }
</style>
</head>
<body>
  <div class="side-label side-label--front">Front</div>
  <div class="side-label side-label--back">Back</div>

  <section class="card card--light card--front-cover">
    <div class="brand"><span class="brand__square"></span>KORVANEX</div>
  </section>

  <section class="card card--light card--front-inside">
    <p class="mission">KORVANEX is the leading building services innovator. By combining technology with functional toos that improve efficiency in the workplace, we provide unparalleled service in the industry. Developing lasting relationships with our clients and associates is the cornerstone of our success.</p>
  </section>

  <section class="card card--dark card--back-cover">
    <div class="brand"><span class="brand__square"></span>KORVANEX</div>
    <p class="tagline">Where Care Finds Its Pulse</p>
  </section>

  <section class="card card--dark card--back-details">
    <div class="brand"><span class="brand__square"></span>KORVANEX</div>
    <div class="holder">Your Name, <span class="holder__role">Designation</span></div>
    <div class="contact contact--phones">
      <div class="contact__row">
        <svg class="contact__icon" viewBox="0 0 10 10"><rect x="2.5" y="0.5" width="5" height="9" rx="1" fill="#fff"/></svg>
        <span>+12 345 67 8910</span>
      </div>
      <div class="contact__row">
        <svg class="contact__icon" viewBox="0 0 10 10"><path d="M2 1 L4 1 L5 3.5 L3.8 4.5 Q5 6.5 6 6.5 L7 5.5 L9 6.5 L9 8.5 Q4 9.5 1 2 Z" fill="#fff"/></svg>
        <span>+12 345 67 8910</span>
      </div>
    </div>
    <div class="contact contact--web">
      <div class="contact__row">
        <svg class="contact__icon" viewBox="0 0 10 10"><rect x="0.5" y="2" width="9" height="6" fill="#fff"/><path d="M0.5 2 L5 5.5 L9.5 2" stroke="#000" stroke-width="1" fill="none"/></svg>
        <span>info@korvanex-demo.net</span>
      </div>
      <div class="contact__row">
        <svg class="contact__icon" viewBox="0 0 10 10"><circle cx="5" cy="5" r="4.5" fill="#fff"/><path d="M0.5 5 H9.5 M5 0.5 V9.5" stroke="#000" stroke-width="0.8"/></svg>
        <span>www.korvanex-demo.net</span>
      </div>
    </div>
    <div class="contact contact--address">123, Abc Street<br>0000 City, Country</div>
  </section>
</body>
</html>
```